Business Card Design

New business card design

Target Market(s)

Residential & Commercial Property Managers

Industry/Entity Type

Plumbing Services

Contact Information for Business Card

Name - Rowan Keddle, title - Director, Phone Number - 0431 286 517, email - rowan@tbk-plumbing.com.au, Company ABN - 73 215 904 386,

Font styles to use
Sans Serif

Colors
0054AA
0677BA
7BADD7
CADEEF
E8F1F8

```html
<!DOCTYPE html>
<html lang="en">
<head>
<meta charset="utf-8">
<title>TBK Plumbing Services – Business Card</title>
<link href="https://fonts.googleapis.com/css2?family=Roboto:wght@300;400&family=Rubik:wght@500&display=swap" rel="stylesheet">
<style>
  :root {
    --blue-deep: #0054AA;
    --blue: #0677BA;
    --blue-bright: #1fa3dc;
    --blue-soft: #7BADD7;
    --blue-pale: #CADEEF;
    --blue-mist: #E8F1F8;
    --ink: #222326;
    --ink-soft: #5a5d63;
    --backdrop: #e9e6e2;
    --card: #f6f7f8;
  }
  * { box-sizing: border-box; margin: 0; padding: 0; }
  html, body {
    width: 1200px; height: 1054px; overflow: hidden;
    background: var(--backdrop);
  }
  .canvas { position: relative; width: 1200px; height: 1054px; }

  .card {
    position: absolute; left: 100px; top: 225px;
    width: 1000px; height: 604px;
    background: var(--card);
    border-radius: 22px;
    overflow: hidden;
    box-shadow: 0 10px 30px rgba(0,0,0,0.12);
    font-family: "Roboto", Arial, sans-serif;
    color: var(--ink);
  }

  .brand-mark-area {
    position: absolute; left: 28px; top: 40px;
    width: 400px; height: 540px;
    border-radius: 50% 50% 48% 48% / 40% 40% 60% 60%;
    background: radial-gradient(ellipse at 50% 70%, var(--blue-pale) 0%, var(--blue-mist) 60%, rgba(232,241,248,0) 100%);
  }

  .base-band {
    position: absolute; left: 0; bottom: 0;
    width: 100%; height: 22px;
    background: linear-gradient(90deg, var(--blue-bright), var(--blue));
  }

  .info {
    position: absolute; right: 54px; top: 48px;
    text-align: right;
  }
  .company-name {
    font-weight: 300; font-size: 96px; line-height: 1;
    letter-spacing: 0.04em; color: var(--ink);
  }
  .company-tagline {
    margin-top: 18px;
    font-weight: 300; font-size: 17px;
    letter-spacing: 0.62em; margin-right: -0.62em;
    color: var(--ink-soft);
  }
  .person-name {
    margin-top: 76px;
    font-family: "Rubik", Arial, sans-serif; font-weight: 500;
    font-size: 37px; line-height: 1.1; color: var(--ink);
  }
  .person-title {
    margin-top: 6px;
    font-weight: 300; font-size: 23px; color: var(--ink-soft);
  }
  .address {
    margin-top: 40px;
    font-weight: 300; font-size: 23px; line-height: 36px; color: var(--ink);
  }
  .contact-list { list-style: none; margin-top: 10px; }
  .contact-item {
    display: flex; justify-content: flex-end; align-items: center;
    gap: 16px; height: 36px;
    font-weight: 300; font-size: 23px; color: var(--ink);
  }
  .contact-icon { width: 20px; height: 20px; fill: var(--blue-bright); flex: none; }
</style>
</head>
<body>
<div class="canvas">
  <section class="card">
    <div class="brand-mark-area" role="img" aria-label="Large brand symbol decoration in bright blue"></div>

    <div class="info">
      <div class="company-name">TBK</div>
      <div class="company-tagline">plumbing services</div>

      <div class="person-name">Rowan Keddle</div>
      <div class="person-title">Managing Director</div>

      <div class="address">18 Riverbend Rd., Fairfield,<br>Melbourne, VIC 3078</div>

      <ul class="contact-list">
        <li class="contact-item">0431 286 517
          <svg class="contact-icon" viewBox="0 0 20 20" aria-hidden="true"><path d="M2 7c0-3 3-4 8-4s8 1 8 4v1h-4V6H6v2H2zM4 10h12l1 7H3zm6 2a2 2 0 1 0 0 4 2 2 0 0 0 0-4z"/></svg>
        </li>
        <li class="contact-item">rowan@tbk-plumbing.com.au
          <svg class="contact-icon" viewBox="0 0 20 20" aria-hidden="true"><path d="M2 4h16v12H2zm1.5 1.5L10 11l6.5-5.5z"/></svg>
        </li>
        <li class="contact-item">www.tbk-plumbing.com.au
          <svg class="contact-icon" viewBox="0 0 20 20" aria-hidden="true"><circle cx="10" cy="10" r="8" fill="none" stroke="var(--blue-bright)" stroke-width="2"/><path d="M2 10h16M10 2c-4 5-4 11 0 16M10 2c4 5 4 11 0 16" fill="none" stroke="var(--blue-bright)" stroke-width="1.5"/></svg>
        </li>
      </ul>
    </div>

    <div class="base-band"></div>
  </section>
</div>
</body>
</html>
```